BOLD & MINIMALIST DESIGN NEEDED

We want a very bold but minimalistic business card design that is impactful and utilizes both sides of the business card. Our current logo is included for your use.

We want bold fonts and good use of negative space. We don't want the logo to overpower the design.

Target Market(s)

Professionals who are building new commercial buildings.

Industry/Entity Type

Construction

Contact Information for Business Card

Name, Title, email, office phone, cell phone, website

Font styles to use
Serif
Sans Serif

Requirements
Must have
• Bold design!

```html
<!DOCTYPE html>
<html lang="en">
<head>
<meta charset="utf-8">
<title>Ridgeline Design + Build — Business Card</title>
<link href="https://fonts.googleapis.com/css2?family=Oswald:wght@700&family=Montserrat:wght@400;700&display=swap" rel="stylesheet">
<style>
  :root {
    --bg: #d3d4cf;
    --card-white: #ffffff;
    --brand-green: #7dc02a;
    --green-deep: #6aa522;
    --green-pale: #e4f1d6;
    --ink: #1b1b1b;
    --mark-grey: #d2d2d2;
  }
  * { box-sizing: border-box; margin: 0; padding: 0; }
  html, body { width: 1200px; height: 801px; overflow: hidden; }
  body {
    background: var(--bg);
    font-family: "Montserrat", Arial, sans-serif;
    display: flex; align-items: center; justify-content: center; gap: 40px;
  }
  .card {
    position: relative;
    width: 540px; height: 309px;
    overflow: hidden;
    box-shadow: 0 10px 24px rgba(0,0,0,.18);
  }
  .card--front { background: var(--card-white); }
  .card--back { background: var(--brand-green); }

  .front__mark-area {
    position: absolute; left: 150px; bottom: 0;
    width: 230px; height: 190px;
    background: linear-gradient(135deg, var(--mark-grey), #e6e6e6 70%, var(--green-pale));
    opacity: .7;
  }
  .front__tab {
    position: absolute; left: 0; top: 128px;
    width: 12px; height: 40px;
    background: var(--brand-green);
    border-radius: 0 8px 8px 0;
  }
  .identity { position: absolute; left: 34px; top: 118px; }
  .identity__name {
    font-family: "Oswald", Impact, sans-serif; font-weight: 700;
    font-size: 34px; line-height: 1; letter-spacing: .5px;
    color: var(--brand-green); text-transform: uppercase;
  }
  .identity__title {
    margin-top: 6px; font-size: 13px; letter-spacing: 1px;
    color: var(--ink); text-transform: uppercase;
  }

  .brand {
    position: absolute; right: 34px; top: 38px; width: 230px;
    display: flex; align-items: center; gap: 10px;
  }
  .brand__square { width: 26px; height: 26px; background: var(--ink); flex: none; }
  .brand__name {
    font-family: "Oswald", Impact, sans-serif; font-weight: 700;
    font-size: 22px; line-height: 1.1; color: var(--ink); text-transform: uppercase;
  }

  .contact {
    position: absolute; right: 34px; top: 150px; width: 230px;
    list-style: none; font-size: 12px; color: var(--ink);
  }
  .contact li { display: flex; align-items: center; gap: 8px; margin-bottom: 7px; }
  .contact svg { width: 13px; height: 13px; flex: none; }
  .contact .accent { color: var(--brand-green); }

  .back__pattern {
    position: absolute; inset: 0;
    background:
      radial-gradient(ellipse at 30% 40%, rgba(255,255,255,.08), transparent 60%),
      linear-gradient(160deg, var(--brand-green), var(--green-deep));
  }
  .back__brand {
    position: absolute; right: 36px; bottom: 34px;
    font-family: "Oswald", Impact, sans-serif; font-weight: 700;
    font-size: 16px; color: var(--card-white); text-transform: uppercase;
  }
</style>
</head>
<body>
  <section class="card card--front" aria-label="Card front">
    <div class="front__mark-area" role="img" aria-label="Large faint company mark in grey and pale green"></div>
    <div class="front__tab"></div>

    <div class="identity">
      <p class="identity__name">Mark Delaney</p>
      <p class="identity__title">Owner</p>
    </div>

    <div class="brand">
      <span class="brand__square"></span>
      <span class="brand__name">Ridgeline Design + Build</span>
    </div>

    <ul class="contact">
      <li>
        <svg viewBox="0 0 16 16"><path fill="var(--brand-green)" d="M3 1l3 3-2 2c1 2 3 4 5 5l2-2 3 3-2 3C6 14 2 10 1 3z"/></svg>
        (555) 014-2287
      </li>
      <li>
        <svg viewBox="0 0 16 16"><rect x="2" y="6" width="12" height="8" rx="1" fill="var(--brand-green)"/><path d="M1 6c2-4 12-4 14 0" stroke="var(--brand-green)" stroke-width="2" fill="none"/></svg>
        (555) 014-2287
      </li>
      <li>
        <svg viewBox="0 0 16 16"><rect x="1.5" y="3.5" width="13" height="9" fill="none" stroke="var(--brand-green)" stroke-width="1.5"/><path d="M1.5 3.5l6.5 5 6.5-5" fill="none" stroke="var(--brand-green)" stroke-width="1.5"/></svg>
        ridgelinebuild@mail.com
      </li>
      <li>
        <svg viewBox="0 0 16 16"><circle cx="8" cy="8" r="6.5" fill="none" stroke="var(--brand-green)" stroke-width="1.5"/><path d="M1.5 8h13M8 1.5c-3 3-3 10 0 13M8 1.5c3 3 3 10 0 13" fill="none" stroke="var(--brand-green)" stroke-width="1.2"/></svg>
        <span>www.<span class="accent">ridgelinebuild</span>.com</span>
      </li>
    </ul>
  </section>

  <section class="card card--back" aria-label="Card back">
    <div class="back__pattern" role="img" aria-label="Embossed repeating pattern of company marks on green"></div>
    <span class="back__brand">Ridgeline Design + Build</span>
  </section>
</body>
</html>
```